Dalvick's Business Card

I need some designs for a new business card including the new logo attached. An old example of our business card is also attached to show all the data that should be included on the new design.
**I added some more examples someone had mocked up**

Contact Information for Business Card

Should include all info on other examples uploaded.

```html
<!DOCTYPE html>
<html lang="en">
<head>
<meta charset="utf-8">
<title>Dalvick's Business Card</title>
<link href="https://fonts.googleapis.com/css2?family=Montserrat:wght@500;600;700&family=Oswald:wght@500;600&display=swap" rel="stylesheet">
<style>
  :root {
    --brand-blue: #0a6cb5;
    --brand-blue-deep: #0962a6;
    --brand-red: #e3202a;
    --paper: #ffffff;
    --ink: #1f2a36;
    --stage: #e6e8eb;
    --rule: #8a9099;
  }
  * { margin: 0; padding: 0; box-sizing: border-box; }
  html, body { width: 1200px; height: 1200px; overflow: hidden; }
  body {
    background: var(--stage);
    font-family: "Montserrat", Arial, sans-serif;
    position: relative;
  }
  .card {
    position: absolute;
    left: 300px;
    width: 600px;
    height: 343px;
    border-radius: 22px;
    overflow: hidden;
  }
  .card--front { top: 150px; background: var(--paper); box-shadow: 0 6px 18px rgba(0,0,0,.12); }
  .card--back { top: 553px; background: var(--brand-blue); box-shadow: 0 6px 18px rgba(0,0,0,.12); }

  .brand {
    position: absolute;
    display: flex;
    align-items: center;
    gap: 14px;
  }
  .brand__dot { width: 46px; height: 46px; border-radius: 50%; }
  .brand__name { font-weight: 700; letter-spacing: 1px; line-height: 1; }

  .card--front .brand { top: 52px; left: 0; right: 0; justify-content: center; }
  .card--front .brand__dot { background: var(--brand-red); }
  .card--front .brand__name { color: var(--brand-blue); font-size: 56px; }

  .contact { position: absolute; left: 42px; top: 196px; }
  .contact__name { color: var(--brand-blue); font-weight: 600; font-size: 23px; letter-spacing: .5px; margin-bottom: 10px; }
  .contact__line { display: flex; align-items: center; gap: 10px; font-size: 14px; color: var(--ink); margin-bottom: 6px; font-weight: 500; }
  .contact__line svg { width: 16px; height: 16px; flex: none; }

  .divider { position: absolute; left: 330px; top: 190px; width: 1px; height: 82px; background: var(--rule); }

  .credentials { position: absolute; left: 356px; top: 196px; font-family: "Oswald", "Arial Narrow", sans-serif; text-transform: uppercase; line-height: 1.15; }
  .credentials__licensed { color: var(--brand-blue); font-size: 24px; font-weight: 500; }
  .credentials__family { color: var(--brand-red); font-size: 27px; font-weight: 600; }

  .bands { position: absolute; left: 0; bottom: 0; width: 600px; height: 30px; }

  .card--back .brand { top: 112px; left: 0; right: 0; justify-content: center; }
  .card--back .brand__dot { background: var(--paper); }
  .card--back .brand__name { color: var(--paper); font-size: 72px; }

  .service-area {
    position: absolute; left: 0; right: 0; bottom: 46px; text-align: center;
    font-family: "Oswald", "Arial Narrow", sans-serif; font-weight: 500;
    color: var(--paper); font-size: 24px; letter-spacing: .5px; text-transform: uppercase;
  }
</style>
</head>
<body>
  <section class="card card--front">
    <div class="brand">
      <span class="brand__dot"></span>
      <span class="brand__name">DALVICK'S</span>
    </div>

    <div class="contact">
      <p class="contact__name">MARK DALVICK</p>
      <p class="contact__line">
        <svg viewBox="0 0 24 24" aria-hidden="true"><path fill="#0a6cb5" d="M6.6 10.8a15 15 0 0 0 6.6 6.6l2.2-2.2c.3-.3.7-.4 1-.2 1.1.4 2.3.6 3.6.6.6 0 1 .4 1 1V20c0 .6-.4 1-1 1A17 17 0 0 1 3 4c0-.6.4-1 1-1h3.5c.6 0 1 .4 1 1 0 1.3.2 2.5.6 3.6.1.3 0 .7-.2 1z"/></svg>
        555.014.2290
      </p>
      <p class="contact__line">
        <svg viewBox="0 0 24 24" aria-hidden="true"><path fill="#0a6cb5" d="M2 5h20v14H2z"/><path fill="none" stroke="#fff" stroke-width="1.6" d="M2.5 5.5 12 13l9.5-7.5"/></svg>
        hvacdalvick@mailbox.com
      </p>
      <p class="contact__line">
        <svg viewBox="0 0 24 24" aria-hidden="true"><g fill="none" stroke="#0a6cb5" stroke-width="1.8"><circle cx="12" cy="12" r="9.5"/><ellipse cx="12" cy="12" rx="4" ry="9.5"/><path d="M2.5 12h19M4 7h16M4 17h16"/></g></svg>
        www.dalvickhvac.com
      </p>
    </div>

    <div class="divider"></div>

    <div class="credentials">
      <p class="credentials__licensed">Licensed &amp; Insured</p>
      <p class="credentials__family">Family Owned &amp; Operated</p>
    </div>

    <svg class="bands" viewBox="0 0 600 30" preserveAspectRatio="none" aria-hidden="true">
      <polygon points="0,18 340,18 334,30 0,30" fill="var(--brand-blue)"/>
      <polygon points="346,8 600,8 600,30 340,30" fill="var(--brand-red)"/>
    </svg>
  </section>

  <section class="card card--back">
    <div class="brand">
      <span class="brand__dot"></span>
      <span class="brand__name">DALVICK'S</span>
    </div>
    <p class="service-area">Serves Ferndale, IA &amp; Surrounding Areas</p>
  </section>
</body>
</html>
```